Kestrelford Therapy and Consulting

Build & publish a WordPress website that advertises and markets my private practice - which is delivering, and consulting in, psychological therapies. I also need to be able to edit content (eg text and images) on the end product thereafter. It should have a call to action on the homepage, links to:
• About me
• For referrers (with link to service fees)
• Contact details – phone#, email address, location, operating hours, and service fees
• Other resources

Target Market(s)

People struggling with mental health, relationships, and/or psychological disorders

Industry/Entity Type

Mental health

Coding

Coded - Design and coding required

Number of Pages Required

4 page

Requirements
Must have
• WordPress
Nice to have
• Please make my logo standout on the home page
Should not have
• No testimonials - they're forbidden for psychologists in Australia

```html
<!DOCTYPE html>
<html lang="en">
<head>
<meta charset="utf-8">
<title>Kestrelford Therapy and Consulting</title>
<link rel="stylesheet" href="https://fonts.googleapis.com/css2?family=Lato:wght@400;700&family=Playfair+Display:wght@400;700&display=swap">
<style>
:root{
  --cyan:#2ec6da;
  --pink:#e062d2;
  --blue:#5a9bd8;
  --heading:#4d9fd3;
  --ink:#2b2b2b;
  --muted:#7a7a7a;
  --phone:#1f6fc0;
  --pale:#f2f8f8;
  --white:#ffffff;
  --grad:linear-gradient(90deg,var(--cyan),var(--pink));
}
*{box-sizing:border-box;margin:0;padding:0}
html,body{width:1200px;height:3933px;overflow:hidden;background:var(--white)}
body{font-family:'Lato',sans-serif;color:var(--ink);position:relative}
.abs{position:absolute}
.serif{font-family:'Playfair Display',serif}
section,header,footer{position:absolute;left:0;width:1200px}
.dots{position:absolute;height:3px;background-image:radial-gradient(circle,var(--cyan) 1.2px,transparent 1.6px);background-size:8px 3px}
.btn{position:absolute;height:47px;border-radius:24px;color:var(--white);font-weight:700;font-size:15px;display:flex;align-items:center;justify-content:center;background:var(--grad)}
.h2{position:absolute;font-family:'Playfair Display',serif;font-weight:700;color:var(--heading);font-size:44px;line-height:56px}
.tick{position:absolute;width:13px;height:13px;border-radius:50%;border:1.6px solid var(--cyan)}
.tick::after{content:"";position:absolute;left:3px;top:1.5px;width:3px;height:5.5px;border-right:1.6px solid var(--pink);border-bottom:1.6px solid var(--pink);transform:rotate(45deg)}
.list{position:absolute;font-size:15px;line-height:20px}
.brand-name{font-family:'Lato',sans-serif;font-weight:400;color:var(--heading)}
.brand-dot{border-radius:50%;border:2px solid var(--heading)}

/* header + hero */
.hero{top:0;height:527px;background:var(--pale)}
.logo{left:118px;top:28px;display:flex;align-items:center;gap:12px}
.logo .brand-dot{width:34px;height:34px}
.logo .brand-name{font-size:28px}
.nav{left:486px;top:43px;font-size:15px}
.nav a{position:absolute;white-space:nowrap;color:var(--ink);text-decoration:none}
.call{left:922px;top:30px}
.call .circle{position:absolute;left:0;top:2px;width:44px;height:44px;border-radius:50%;background:linear-gradient(135deg,var(--cyan),var(--pink));display:flex;align-items:center;justify-content:center}
.call .label{position:absolute;left:55px;top:4px;font-size:15px;color:#555;white-space:nowrap}
.call .num{position:absolute;left:55px;top:24px;font-size:18px;font-weight:700;color:var(--phone);white-space:nowrap}
.hero-art{left:99px;top:84px;width:458px;height:443px;border-radius:220px 220px 0 0;background:linear-gradient(90deg,#e06a55 0%,#e06a55 45%,#3a3a3a 55%,#35707f 65%,#35707f 100%)}
.welcome{left:637px;top:196px;font-size:42px;color:var(--ink)}
.hero-title{left:635px;top:243px;font-size:84px;font-weight:700;line-height:100px;color:#1b1b1b}
.hero-sub{left:637px;top:336px;font-size:50px;color:var(--ink)}

/* profile */
.profile{top:527px;height:514px;background:linear-gradient(100deg,var(--cyan) 0%,#b89ad6 55%,var(--pink) 100%);border-top-left-radius:80px;color:var(--white)}
.profile .name{left:115px;top:84px;font-size:44px;font-weight:700}
.profile .role{left:115px;top:145px;font-size:17px;font-weight:700}
.profile .bio{left:111px;top:190px;width:512px;font-size:15.3px;line-height:28.3px}
.profile .outline{position:absolute;left:111px;top:383px;width:150px;height:47px;border:2px solid var(--white);border-radius:24px;display:flex;align-items:center;justify-content:center;font-weight:700;font-size:15px}
.portrait{left:745px;top:81px;width:342px;height:342px;border-radius:50%;background:radial-gradient(circle at 50% 40%,#c9a48c 0%,#6e7c5c 55%,#2f4a3a 100%)}

/* services */
.services{top:1041px;height:567px}
.services .h2{left:0;width:1200px;text-align:center;top:59px}
.services .intro{left:264px;top:150px;width:672px;text-align:center;font-size:14.5px;line-height:29px}
.wheel{left:252px;top:227px}
.seg-label{position:absolute;font-family:'Playfair Display',serif;color:var(--white);font-size:15px;line-height:22px;text-align:center;white-space:nowrap}
.centre-logo{left:490px;top:478px;display:flex;align-items:center;gap:10px}
.centre-logo .brand-dot{width:30px;height:30px}
.centre-logo .brand-name{font-size:28px}

/* areas */
.areas{top:1608px;height:504px;background:var(--pale)}
.photo-ring{border-radius:50%}
.areas .ring{left:116px;top:71px;width:386px;height:386px;border:3px solid var(--pink)}
.areas .photo{left:112px;top:71px;width:380px;height:380px;background:radial-gradient(circle at 50% 35%,#a57a5c 0%,#d8ccc0 45%,#ece7e1 100%)}

/* modalities */
.modalities{top:2112px;height:553px}
.modalities .ring{left:681px;top:98px;width:392px;height:392px;border:3px solid var(--pink)}
.modalities .photo{left:689px;top:98px;width:390px;height:390px;background:radial-gradient(circle at 50% 40%,#b08a72 0%,#8c8f94 45%,#3b3a38 100%)}
.modalities .text{left:111px;top:316px;width:540px;font-size:15px;line-height:28.5px}

/* fees */
.fees{top:2665px;height:549px;background:var(--pale)}
.card{left:224px;top:81px;width:753px;height:384px;background:var(--white);border-radius:12px;box-shadow:0 6px 24px rgba(0,0,0,.08)}
.card .h2{left:0;width:753px;text-align:center;top:38px}
.card .dots{left:330px;width:93px;top:119px}
.card .main{left:96px;top:149px;width:561px;text-align:center;font-size:15px;line-height:28.5px}
.hl-pink{color:var(--pink)}
.hl-cyan{color:var(--cyan)}
.card .small{left:96px;top:260px;width:561px;text-align:center;font-size:12.5px;line-height:24.5px;color:var(--muted)}

/* referrers */
.referrers{top:3214px;height:283px}
.referrers .text{left:411px;top:70px;width:680px;font-size:15px;line-height:28.5px}

/* footer */
.footer{top:3497px;height:436px;background:linear-gradient(100deg,var(--cyan) 0%,#b39bd6 55%,var(--pink) 100%);border-top-left-radius:80px;color:var(--white)}
.footer .flogo{left:111px;top:104px;display:flex;align-items:center;gap:12px}
.footer .flogo .brand-dot{width:40px;height:40px;border-color:var(--white)}
.footer .flogo .brand-name{color:var(--white);font-size:32px}
.footer .fcall{left:928px;top:94px}
.footer .fcall .circle{position:absolute;left:0;top:0;width:42px;height:42px;border-radius:50%;border:2px solid var(--white);display:flex;align-items:center;justify-content:center}
.footer .fcall .label{position:absolute;left:54px;top:1px;font-size:15px;white-space:nowrap}
.footer .fcall .num{position:absolute;left:54px;top:20px;font-size:18px;font-weight:700;white-space:nowrap}
.fcol{position:absolute;font-size:15px;line-height:26px}
.fcol b{font-weight:700}
.fnote{position:absolute;font-size:12.5px;line-height:24.5px}
.fhead{position:absolute;font-size:17px;font-weight:700}
.flinks{position:absolute;font-size:15px;line-height:28.5px}
.copy{left:0;width:1200px;text-align:center;top:384px;font-size:13px}
</style>
</head>
<body>

<header class="hero">
  <div class="abs logo"><span class="brand-dot"></span><span class="brand-name">Kestrelford</span></div>
  <nav class="abs nav">
    <a style="left:0;font-weight:700">Home</a>
    <a style="left:64px">About Me</a>
    <a style="left:151px">For Referrers</a>
    <a style="left:262px">Resources</a>
    <a style="left:354px">Contact</a>
  </nav>
  <div class="abs call">
    <div class="circle"><svg width="20" height="20" viewBox="0 0 24 24"><path fill="#fff" d="M6.6 10.8a15.1 15.1 0 0 0 6.6 6.6l2.2-2.2c.3-.3.7-.4 1-.2 1.1.4 2.3.6 3.6.6.6 0 1 .4 1 1V20c0 .6-.4 1-1 1A17 17 0 0 1 3 4c0-.6.4-1 1-1h3.5c.6 0 1 .4 1 1 0 1.3.2 2.5.6 3.6.1.3 0 .7-.2 1z"/></svg></div>
    <div class="label">Call Today:</div>
    <div class="num">0491 570 156</div>
  </div>
  <div class="abs hero-art" role="img" aria-label="Illustration of two head silhouettes in coral and teal facing opposite ways, with line-drawn brains"></div>
  <div class="abs serif welcome">Welcome to</div>
  <div class="abs serif hero-title">Kestrelford</div>
  <div class="abs serif hero-sub">Therapy &amp; Consulting</div>
</header>

<section class="profile">
  <div class="abs serif name">Mr Daniel Hartley</div>
  <div class="abs role">Clinical Psychologist, Clinical Supervisor</div>
  <p class="abs bio">I’m a clinical psychologist, psychotherapist, EMDR Consultant, and Resource Therapy Practitioner and Trainer. My main interest in therapy is helping people overcome the inner obstacles that cause them emotional pain and suffering, and that maintain behavioural patterns that are damaging or self-defeating. I also like to train, coach and mentor other therapists in effective therapies.</p>
  <div class="outline">Learn More</div>
  <div class="abs portrait" role="img" aria-label="Portrait photo of the psychologist outdoors against greenery"></div>
</section>

<section class="services">
  <h2 class="h2">Our Services</h2>
  <div class="dots" style="left:519px;width:163px;top:127px"></div>
  <p class="abs intro">I provide trauma-focused psychotherapy to clients and consult with other mental health clinicians on their practice of psychotherapy.</p>
  <svg class="abs wheel" width="700" height="340" viewBox="0 0 700 340" aria-hidden="true">
    <path fill="#2ec6da" d="M56 340 A294 294 0 0 1 90.4 202 L206.1 263.5 A163 163 0 0 0 187 340 Z"/>
    <path fill="#e062d2" d="M80.7 184.5 A311 311 0 0 1 233.5 51.6 L288.9 188.9 A163 163 0 0 0 208.8 258.5 Z"/>
    <path fill="#5a9bd8" d="M462.9 29.9 A330 330 0 0 0 237.1 29.9 L294.3 186.8 A163 163 0 0 1 405.7 186.8 Z"/>
    <path fill="#e062d2" d="M619.3 184.5 A311 311 0 0 0 466.5 51.6 L411.1 188.9 A163 163 0 0 1 491.2 258.5 Z"/>
    <path fill="#2ec6da" d="M644 340 A294 294 0 0 0 609.6 202 L493.9 263.5 A163 163 0 0 1 513 340 Z"/>
  </svg>
  <div class="seg-label" style="left:308px;top:528px;width:140px">Psychotherapy</div>
  <div class="seg-label" style="left:376px;top:392px;width:140px">Professional<br>Training</div>
  <div class="seg-label" style="left:532px;top:330px;width:140px">Online Video<br>Consultations</div>
  <div class="seg-label" style="left:688px;top:392px;width:140px">Clinical<br>Supervision</div>
  <div class="seg-label" style="left:757px;top:528px;width:140px">Assessment</div>
  <div class="abs centre-logo"><span class="brand-dot"></span><span class="brand-name">Kestrelford</span></div>
</section>

<section class="areas">
  <div class="abs photo-ring ring"></div>
  <div class="abs photo-ring photo" role="img" aria-label="Photo of a smiling woman in a cream sweater sitting at a laptop"></div>
  <h2 class="h2" style="left:603px;top:47px">Areas of<br>Special Interest</h2>
  <div class="dots" style="left:603px;width:117px;top:178px"></div>
  <span class="tick" style="left:600px;top:234px"></span>
  <span class="tick" style="left:600px;top:263px"></span>
  <span class="tick" style="left:600px;top:291px"></span>
  <span class="tick" style="left:600px;top:320px"></span>
  <span class="tick" style="left:600px;top:348px"></span>
  <div class="list" style="left:628px;top:231px;line-height:28.4px">Addiction<br>Anger Related Issues<br>Anxiety / Panic Attacks<br>Assertiveness<br>Borderline Personality</div>
  <span class="tick" style="left:831px;top:234px"></span>
  <span class="tick" style="left:831px;top:263px"></span>
  <span class="tick" style="left:831px;top:291px"></span>
  <span class="tick" style="left:831px;top:320px"></span>
  <span class="tick" style="left:831px;top:348px"></span>
  <div class="list" style="left:860px;top:231px;line-height:28.4px">Depression<br>Dissociative Disorders<br>Dual Diagnosis<br>Existential Issues<br>Grief / Bereavement</div>
  <div class="btn" style="left:602px;top:409px;width:149px">Learn More</div>
</section>

<section class="modalities">
  <h2 class="h2" style="left:113px;top:59px">Modalities</h2>
  <div class="dots" style="left:113px;width:163px;top:137px"></div>
  <span class="tick" style="left:113px;top:187px"></span>
  <span class="tick" style="left:113px;top:215px"></span>
  <span class="tick" style="left:113px;top:243px"></span>
  <span class="tick" style="left:113px;top:271px"></span>
  <div class="list" style="left:142px;top:184px;line-height:28.2px">EMDR<br>Existential<br>Integrative<br>Mindfulness</div>
  <span class="tick" style="left:276px;top:187px"></span>
  <span class="tick" style="left:276px;top:215px"></span>
  <span class="tick" style="left:276px;top:243px"></span>
  <span class="tick" style="left:276px;top:271px"></span>
  <div class="list" style="left:305px;top:184px;line-height:28.2px">Person Centred<br>Psychodynamic<br>Schema Therapy<br>CBT</div>
  <p class="abs text">I believe that using Eye Movement Desensitizing and Reprocessing (EMDR) therapy and Resource Therapy (RT) together addresses almost all mental illness that doesn’t involve an organic component.</p>
  <div class="btn" style="left:111px;top:421px;width:151px">Learn More</div>
  <div class="abs photo-ring ring"></div>
  <div class="abs photo-ring photo" role="img" aria-label="Photo of a relaxed man with hands behind his head and eyes closed"></div>
</section>

<section class="fees">
  <div class="abs card">
    <h2 class="h2">Fees</h2>
    <div class="dots"></div>
    <p class="abs main">My standard fee for a <span class="hl-pink">50 to 60 minute</span> psychological therapy session is <span class="hl-pink">$220</span>. For those who are on <span class="hl-cyan">low or no income</span> my concession fee is <span class="hl-cyan">$180</span>. Medicare currently rebates 137.05 for a 50+ minute psychological therapy session if a MHCP is in place.</p>
    <p class="abs small">PAYMENT OPTIONS: I currently accept EFT transfers only. I can process Medicare webclaims online on behalf of clients where they are registered with Medicare, i.e. Medicare already have their bank account details on file to be able to deposit the rebate into.</p>
  </div>
</section>

<section class="referrers">
  <h2 class="h2" style="left:113px;top:72px">For referrers</h2>
  <div class="dots" style="left:113px;width:163px;top:149px"></div>
  <p class="abs text">Lorem ipsum dolor sit amet, consectetur adipiscing elit, sed do eiusmod tempor incididunt ut labore et dolore magna aliqua. Ut enim ad minim veniam, quis nostrud exercitation ullamco laboris nisi ut lore aliquip ex ea commodo consequat.</p>
  <div class="btn" style="left:411px;top:176px;width:151px">Service Fees</div>
</section>

<footer class="footer">
  <div class="abs flogo"><span class="brand-dot"></span><span class="brand-name">Kestrelford</span></div>
  <div class="abs fcall">
    <div class="circle"><svg width="20" height="20" viewBox="0 0 24 24"><path fill="#fff" d="M6.6 10.8a15.1 15.1 0 0 0 6.6 6.6l2.2-2.2c.3-.3.7-.4 1-.2 1.1.4 2.3.6 3.6.6.6 0 1 .4 1 1V20c0 .6-.4 1-1 1A17 17 0 0 1 3 4c0-.6.4-1 1-1h3.5c.6 0 1 .4 1 1 0 1.3.2 2.5.6 3.6.1.3 0 .7-.2 1z"/></svg></div>
    <div class="label">Call Today:</div>
    <div class="num">0491 570 156</div>
  </div>

  <svg class="abs" style="left:112px;top:198px" width="14" height="18" viewBox="0 0 14 18" aria-hidden="true"><path fill="#fff" d="M7 0a7 7 0 0 0-7 7c0 5 7 11 7 11s7-6 7-11a7 7 0 0 0-7-7zm0 9.5A2.5 2.5 0 1 1 7 4.5a2.5 2.5 0 0 1 0 5z"/></svg>
  <div class="fcol" style="left:144px;top:196px"><b>Suite 4, Harbour House, 18 Wattle Street,<br>Kestrelford, TAS 7000</b></div>
  <p class="fnote" style="left:111px;top:264px;width:330px">* There is limited paid parking in Wattle Street and surrounds but, being adjacent to the GPO, Harbour House is very close to public transport.</p>

  <svg class="abs" style="left:516px;top:199px" width="17" height="17" viewBox="0 0 18 18" aria-hidden="true"><circle cx="9" cy="9" r="8" fill="#fff"/><path d="M9 4v5l3 2" stroke="#b39bd6" stroke-width="1.8" fill="none"/></svg>
  <div class="fcol" style="left:547px;top:196px"><b>9am to 5pm<br>Wednesdays only.</b></div>
  <svg class="abs" style="left:516px;top:270px" width="17" height="13" viewBox="0 0 18 13" aria-hidden="true"><rect width="18" height="13" rx="1.5" fill="#fff"/><path d="M1 1l8 6 8-6" stroke="#b39bd6" stroke-width="1.5" fill="none"/></svg>
  <div class="fcol" style="left:547px;top:263px"><b>Email<br>info@kestrelford.com</b></div>

  <div class="fhead" style="left:770px;top:195px">Quick Links</div>
  <div class="flinks" style="left:770px;top:230px">About me<br>For referrers<br>Contact<br>Other resources</div>
  <div class="fhead" style="left:983px;top:195px">Other Links</div>
  <div class="flinks" style="left:983px;top:230px">Terms<br>Privacy Policy<br>Cookies</div>

  <div class="abs copy">2024 Kestrelford Therapy and Consulting. All Rights Reserved.</div>
</footer>

</body>
</html>
```